Computer Training in the Education sector - Letterhead

We need a new letter head to be designed for the company. We provide computer training fro the Education Sector, both primary and private tertiary providers. The colours will need to tie in with the website www.crossingthestream.co.nz.
The company name is Crossing the Stream with the tag line of Computer Training for Educators.
The footer will need to have the following detail...
0508 PCS MENTOR
021 839 415
www.crossingthestream.co.nz / training@crossingthestream.co.nz
Updates

Thanks for the designs so far.

Some have watermarks in the background. Please don't worry about using watermarks as I will not be using a watermark in in a final design.
Regards,
Roger

Thank you for all the designs and the effort. There was some great concepts that came through.

Cheers
Roger

Industry/Entity Type

Computer

```html
<!DOCTYPE html>
<html lang="en">
<head>
<meta charset="utf-8">
<title>Crossing the Stream — Letterhead</title>
<link href="https://fonts.googleapis.com/css2?family=Libre+Franklin:wght@400;500&display=swap" rel="stylesheet">
<style>
  :root {
    --paper: #ffffff;
    --brand-blue: #2f74b8;
    --accent-orange: #e07f33;
    --accent-green: #7db53f;
    --ink: #3a3a3a;
    --rule-grey: #9a9a9a;
  }
  * { margin: 0; padding: 0; box-sizing: border-box; }
  html, body {
    width: 1034px;
    height: 1200px;
    overflow: hidden;
    background: var(--paper);
    font-family: "Libre Franklin", Arial, sans-serif;
  }
  .letterhead {
    position: relative;
    width: 1034px;
    height: 1200px;
    background: var(--paper);
  }
  .brand-name {
    position: absolute;
    left: 0;
    right: 0;
    top: 70px;
    text-align: center;
    font-size: 32px;
    font-weight: 500;
    line-height: 1.15;
    color: var(--brand-blue);
  }
  .brand-name .line { display: block; }
  .contact-divider {
    position: absolute;
    left: 719px;
    top: 60px;
    width: 1px;
    height: 86px;
    background: var(--rule-grey);
  }
  .contact-list {
    position: absolute;
    left: 738px;
    top: 82px;
    list-style: none;
  }
  .contact-list li {
    display: flex;
    align-items: center;
    gap: 8px;
    height: 23px;
    font-size: 15px;
    color: var(--ink);
  }
  .contact-list svg { width: 13px; height: 13px; flex: none; }
  .footer-rule {
    position: absolute;
    left: 0;
    width: 100%;
    height: 2px;
    background: var(--accent-orange);
  }
  .footer-rule.top { top: 1097px; }
  .footer-rule.bottom { top: 1175px; }
  .tagline-band {
    position: absolute;
    left: 0;
    top: 1105px;
    width: 100%;
    height: 63px;
    background: var(--brand-blue);
    display: flex;
    align-items: center;
    justify-content: center;
    color: #ffffff;
    font-size: 23px;
    letter-spacing: 1.6px;
  }
</style>
</head>
<body>
  <main class="letterhead">
    <header>
      <h1 class="brand-name"><span class="line">Crossing</span><span class="line">the Stream</span></h1>
      <div class="contact-divider"></div>
      <ul class="contact-list">
        <li>
          <svg viewBox="0 0 14 14" aria-hidden="true"><circle cx="7" cy="7" r="6" fill="none" stroke="var(--accent-green)" stroke-width="1.3"/><path d="M5 3.8c-.9.6-1 2 0 3.7s2.3 2.6 3.3 2.5l.8-1-1.3-1-.7.5c-.5-.2-1.2-1-1.4-1.6l.5-.7-.9-1.3z" fill="var(--accent-green)"/></svg>
          021 839 415
        </li>
        <li>
          <svg viewBox="0 0 14 14" aria-hidden="true"><rect x="1" y="3" width="12" height="9" rx="1" fill="var(--accent-green)"/><path d="M1.5 3.8 7 8l5.5-4.2" fill="none" stroke="#fff" stroke-width="1.2"/></svg>
          training@crossingthestream.co.nz
        </li>
        <li>
          <svg viewBox="0 0 14 14" aria-hidden="true" fill="none" stroke="var(--accent-green)" stroke-width="1.1"><circle cx="7" cy="7" r="6"/><ellipse cx="7" cy="7" rx="2.6" ry="6"/><path d="M1 7h12M2 4h10M2 10h10"/></svg>
          www.crossingthestream.co.nz
        </li>
      </ul>
    </header>
    <footer>
      <div class="footer-rule top"></div>
      <div class="tagline-band">Computer Training for Educators</div>
      <div class="footer-rule bottom"></div>
    </footer>
  </main>
</body>
</html>
```